Create Website for new company called "Verdale Lodge 37"

Verdale Lodge 37 is a new business situated in Southwestern Colorado. We are creating a business that will rent out spaces where clients can grow their own marijuana. Picture a large green house with partitioned spaces that are secured by a lock. Best way to envision this would be to think of a storage business that rents out storage rooms. The difference is that we will be having the units inside a green house ( for growing purposes) Picture a small area that is secured by locks, Picture an area that has the ability to provide state of the art security, cameras etc. We want to focus our efforts on professionals, blue collar workers and end users of marijuana. Our emphasis is in the area of assisting those whom wish to grow their own plants. We want to provide them a safe facility in which to do that. . Keep in mind that we also build custom grow rooms at clients homes and provide a grow pod (lease these) where a small grow unit will be delivered and picked up from our clients whom want to lease a unit for a short amount of time. We have a business card ( just designed) and will send that information to those whom express an interests in this project. We want to be able to sign people up for our services by entering an agreement and signing the agreement while on the internet. We want to provide our services to those whom consume recreational and medical marijuana. This site will need to gather information I.e email addresses so that we can followup with offers. This is a tremendous opportunity for the right designer. We will be creating many more websites as other states come on line and make marijuana legal to consume. Use the business card model for a point of reference of how we envision the concept. That is a business card we just recently printed. The hands and the plant is our logo so far. Open to suggestions. There will be three levels of service. Bronze, Silver, Gold or Platinum. We will also have a retail biz down the road but not at the present time.

Target Market(s)

Ages 21-60

Industry/Entity Type

Medical

Logo Text

Verdale Lodge 37.

Number of Pages Required

5+ page

Requirements
Must have
• Clean appearance not to busy , easily navigable from link to link, page to page. Must have ability down the road to enter into a contractual agreement via the website. Must use our provided logo and example of that is on our business card that will be uploaded here shortly. We would like to have the colors that are on the business card however if you have suggestions or color schemes that you want us to consider that is okay.
Nice to have
• Nice to have a animation of seed to weed and how clients can save a tremendous amount of money growing their own cannabis. Nice to have testimonial page or feedback page. Have a membership component to website,
Should not have
• No flashing lights, etc. Not to busy in terms of animations.

```html
<!DOCTYPE html>
<html lang="en">
<head>
<meta charset="utf-8">
<title>Verdale Lodge 37</title>
<link href="https://fonts.googleapis.com/css2?family=Oswald:wght@400;500&family=Arimo:wght@400;700&display=swap" rel="stylesheet">
<style>
:root{
  --page:#2b6d2f;
  --page-dark:#1e5224;
  --footer:#1c4d22;
  --brand:#0a7a35;
  --brand-bright:#14c94e;
  --charcoal:#2f3a38;
  --orange:#db7a33;
  --orange-dark:#a24f16;
  --white:#ffffff;
  --text:#3a3a3a;
  --leaf-light:#7aa35a;
  --leaf-dark:#355e26;
}
*{box-sizing:border-box;margin:0;padding:0}
html,body{width:1024px;height:1200px;overflow:hidden}
body{position:relative;background:var(--page);font-family:"Arimo",Arial,sans-serif;color:var(--text)}
.heading{font-family:"Oswald","Arial Narrow",sans-serif;font-weight:400}
.abs{position:absolute}

/* header */
.logo-panel{left:66px;top:0;width:336px;height:152px}
.logo-name{left:66px;top:50px;width:336px;text-align:center;font-family:"Oswald",sans-serif;font-weight:500;font-size:40px;color:var(--charcoal);letter-spacing:.5px}
.account{right:90px;top:18px;font-family:"Oswald",sans-serif;font-size:14px;color:var(--white)}
.account span{margin:0 4px}
.nav{left:480px;top:74px;display:flex;font-family:"Oswald",sans-serif;font-size:17px;color:var(--white)}
.nav a{color:inherit;text-decoration:none;height:31px;line-height:31px;margin-right:30px}
.nav a.active{background:var(--charcoal);padding:0 19px;margin-right:11px}

/* hero */
.hero-band{left:0;top:172px;width:1024px;height:337px;background:linear-gradient(135deg,var(--leaf-dark),var(--leaf-light) 45%,var(--leaf-dark))}
.slider{left:66px;top:191px;width:607px;height:293px;background:var(--white);padding:9px}
.slide-photo{width:100%;height:100%;position:relative;background:linear-gradient(120deg,#3f5a34,#8fb070 55%,#4d6e3a)}
.slide-caption{position:absolute;left:0;right:0;bottom:0;height:69px;background:rgba(20,20,20,.7);color:var(--white);font-size:25px;text-align:center;line-height:69px}
.arrow{position:absolute;top:112px}
.welcome{left:692px;top:191px;width:266px;height:293px;background:var(--charcoal);padding:9px}
.welcome-inner{background:var(--white);height:100%;padding:0 9px;text-align:center}
.welcome h2{font-size:23px;line-height:30px;color:var(--charcoal);padding-top:1px}
.welcome h3{font-size:23px;line-height:30px;color:var(--brand)}
.welcome p{font-size:11.5px;line-height:15px;letter-spacing:.4px;text-align:left;margin-top:6px}
.btn{display:inline-flex;align-items:center;justify-content:center;gap:6px;font-family:"Oswald",sans-serif;font-size:16px;color:var(--white);height:27px}
.btn-read{background:var(--orange);border:2px solid #f0a070;width:106px;margin-top:8px}

/* services */
.card{top:527px;width:284px;height:188px;background:var(--white);border-radius:4px;overflow:hidden;text-align:center}
.card svg{display:block}
.card h4{position:absolute;top:10px;width:100%;color:var(--white);font-size:22px}
.card p{font-size:11.5px;line-height:15px;letter-spacing:.4px;padding:0 16px;margin-top:6px}
.btn-buy{width:78px;height:25px;margin-top:12px;font-size:16px}
.buy-bronze{background:var(--charcoal);border:2px solid #8a9290}
.buy-silver{background:var(--brand);border:2px solid var(--brand-bright)}
.buy-gold{background:var(--orange);border:2px solid #f0a070}

/* features */
.feature{top:733px;width:426px;height:188px;background:var(--white);border-radius:4px;overflow:hidden}
.feature-side{position:absolute;left:0;top:0}
.feature-photo{position:absolute;top:9px;left:108px;width:130px;height:94px}
.feature h5{position:absolute;top:40px;left:277px;font-size:22px;color:var(--brand)}
.feature p{position:absolute;left:119px;top:109px;width:294px;font-size:11.5px;line-height:15px;letter-spacing:.3px}

/* footer */
.footer{left:0;top:950px;width:1024px;height:186px;background:var(--footer);border-top:1px solid #2f6a34}
.foot-title{font-size:22px;color:var(--orange);position:absolute;top:10px}
.links{list-style:none;position:absolute;left:81px;top:48px;font-family:"Oswald",sans-serif;font-size:14px;color:var(--white);line-height:23px}
.field{position:absolute;left:381px;width:256px;height:27px;background:var(--white);font-size:11.5px;color:#888;padding:7px 8px}
.btn-sub{position:absolute;left:381px;top:135px;width:89px;height:27px;background:var(--brand);border:2px solid var(--brand-bright);font-size:16px}
.contact{position:absolute;left:680px;top:47px;font-family:"Oswald",sans-serif;font-size:14px;color:var(--white);line-height:23px}
.social{position:absolute;left:680px;top:122px;display:flex;gap:18px}
.social span{width:44px;height:44px;border-radius:50%;background:var(--brand);border:2px solid var(--brand-bright);display:flex;align-items:center;justify-content:center}
.social span.first{background:var(--orange);border-color:#f0a070}
.copyright{left:0;top:1160px;width:1024px;text-align:center;font-size:11px;color:var(--white)}
.copyright b{text-decoration:underline}
</style>
</head>
<body>

<header>
  <svg class="abs logo-panel" viewBox="0 0 336 152" aria-hidden="true">
    <polygon points="0,0 336,0 336,116 168,152 0,116" fill="#ffffff"/>
  </svg>
  <div class="abs logo-name">Verdale Lodge 37</div>
  <div class="abs account">Register<span>|</span>Login</div>
  <nav class="abs nav">
    <a class="active" href="#">HOME</a><a href="#">ABOUT</a><a href="#">SERVICES</a><a href="#">TESTIMONIAL</a><a href="#">CONTACT US</a>
  </nav>
</header>

<section>
  <div class="abs hero-band" role="img" aria-label="Background photo of cannabis leaves"></div>
  <div class="abs slider">
    <div class="slide-photo" role="img" aria-label="Photo of hands tending a young cannabis plant">
      <svg class="arrow" style="left:18px" width="20" height="48" viewBox="0 0 20 48"><polyline points="18,2 2,24 18,46" fill="none" stroke="#fff" stroke-width="2"/></svg>
      <svg class="arrow" style="right:18px" width="20" height="48" viewBox="0 0 20 48"><polyline points="2,2 18,24 2,46" fill="none" stroke="#fff" stroke-width="2"/></svg>
      <div class="slide-caption heading">Supporting the care &amp; cultivation of cannabis</div>
    </div>
  </div>
  <div class="abs welcome">
    <div class="welcome-inner">
      <h2 class="heading">Welcome to</h2>
      <h3 class="heading">VERDALE LODGE 37</h3>
      <p>Lorem Ipsum is simply dummy text of the printing and typesetting industry. Lorem Ipsum has been the industry's standard dummy text ever since the 1500s, when an unknown printer took a galley of type and scrambled it to make a type specimen book. It has survived not only five centuries.</p>
      <p style="margin-top:15px">Lorem Ipsum is simply dummy text of the printing and typesetting industry. Lorem Ipsum has been the industry's standard</p>
      <span class="btn btn-read">READ MORE</span>
    </div>
  </div>
</section>

<section>
  <div class="abs card" style="left:68px">
    <svg width="284" height="68" viewBox="0 0 284 68"><polygon points="0,0 284,0 284,42 142,68 0,42" fill="#2f3a38"/></svg>
    <h4 class="heading">Bronze Service</h4>
    <p>Lorem Ipsum is simply dummy text of the printing and typesetting industry. Lorem Ipsum has been the industry's standard dummy text ever since the 1500s, when an unknown printer.</p>
    <span class="btn btn-buy buy-bronze"><svg width="18" height="14" viewBox="0 0 18 14"><path d="M0 1h3l2 8h10l2-6H5" fill="none" stroke="#fff" stroke-width="2"/><circle cx="6" cy="12" r="1.6" fill="#fff"/><circle cx="14" cy="12" r="1.6" fill="#fff"/></svg>BUY</span>
  </div>
  <div class="abs card" style="left:370px">
    <svg width="284" height="68" viewBox="0 0 284 68"><polygon points="0,0 284,0 284,42 142,68 0,42" fill="#0a7a35"/></svg>
    <h4 class="heading">Silver Service</h4>
    <p>Lorem Ipsum is simply dummy text of the printing and typesetting industry. Lorem Ipsum has been the industry's standard dummy text ever since the 1500s, when an unknown printer.</p>
    <span class="btn btn-buy buy-silver"><svg width="18" height="14" viewBox="0 0 18 14"><path d="M0 1h3l2 8h10l2-6H5" fill="none" stroke="#fff" stroke-width="2"/><circle cx="6" cy="12" r="1.6" fill="#fff"/><circle cx="14" cy="12" r="1.6" fill="#fff"/></svg>BUY</span>
  </div>
  <div class="abs card" style="left:672px">
    <svg width="284" height="68" viewBox="0 0 284 68"><polygon points="0,0 284,0 284,42 142,68 0,42" fill="#a24f16"/><polygon points="0,0 284,0 284,38 142,64 0,38" fill="#db7a33"/></svg>
    <h4 class="heading">Gold Service</h4>
    <p>Lorem Ipsum is simply dummy text of the printing and typesetting industry. Lorem Ipsum has been the industry's standard dummy text ever since the 1500s, when an unknown printer.</p>
    <span class="btn btn-buy buy-gold"><svg width="18" height="14" viewBox="0 0 18 14"><path d="M0 1h3l2 8h10l2-6H5" fill="none" stroke="#fff" stroke-width="2"/><circle cx="6" cy="12" r="1.6" fill="#fff"/><circle cx="14" cy="12" r="1.6" fill="#fff"/></svg>BUY</span>
  </div>
</section>

<section>
  <div class="abs feature" style="left:68px">
    <svg class="feature-side" width="110" height="188" viewBox="0 0 110 188">
      <polygon points="0,0 90,0 108,94 90,188 0,188" fill="#0a7a35"/>
      <rect x="12" y="60" width="80" height="68" rx="10" fill="#fff"/>
      <rect x="32" y="54" width="38" height="12" rx="4" fill="#fff"/>
      <circle cx="52" cy="96" r="18" fill="#0a7a35"/><circle cx="52" cy="96" r="10" fill="#fff"/>
    </svg>
    <div class="feature-photo" role="img" aria-label="Photo of a security camera" style="background:linear-gradient(135deg,#e6e6e6,#b9bcbc)"></div>
    <h5 class="heading">Security</h5>
    <p>Lorem Ipsum is simply dummy text of the printing and typesetting industry. Lorem Ipsum has been the industry's standard dummy text Lorem Ipsum is simply ever since Lorem Ipsum is simply dummy text of the.</p>
  </div>
  <div class="abs feature" style="left:530px">
    <svg class="feature-side" width="110" height="188" viewBox="0 0 110 188">
      <polygon points="0,0 90,0 108,94 90,188 0,188" fill="#0a7a35"/>
      <rect x="13" y="58" width="80" height="56" rx="5" fill="#fff"/>
      <rect x="20" y="65" width="66" height="40" fill="#0a7a35"/>
      <rect x="45" y="114" width="16" height="12" fill="#fff"/>
      <rect x="38" y="125" width="30" height="4" fill="#fff"/>
    </svg>
    <div class="feature-photo" role="img" aria-label="Photo of a computer monitor showing a cannabis leaf" style="background:linear-gradient(135deg,#2a2a2a,#5d8a4a 50%,#2a2a2a)"></div>
    <h5 class="heading">Online Access</h5>
    <p>Lorem Ipsum is simply dummy text of the printing and typesetting industry. Lorem Ipsum has been the industry's standard dummy text Lorem Ipsum is simply ever since Lorem Ipsum is simply dummy text of the.</p>
  </div>
</section>

<footer>
  <div class="abs footer">
    <h6 class="heading foot-title" style="left:81px">Useful Links</h6>
    <ul class="links"><li>HOME</li><li>ABOUT</li><li>SERVICES</li><li>TESTIMONIAL</li><li>CONTACT US</li></ul>

    <h6 class="heading foot-title" style="left:383px">Subscribe to our Newsletter</h6>
    <div class="field" style="top:47px">Enter your name</div>
    <div class="field" style="top:91px">Enter your email</div>
    <span class="btn btn-sub">Subscribe</span>

    <h6 class="heading foot-title" style="left:685px">Contact With Us</h6>
    <div class="contact">Office name, Area, City, State, Country<br>123 456 7890<br>info@verdalelodge37.com</div>
    <div class="social">
      <span class="first"></span><span></span><span></span>
      <span><svg width="22" height="16" viewBox="0 0 22 16"><rect x="1" y="1" width="20" height="14" rx="2" fill="#fff"/><polyline points="1,2 11,9 21,2" fill="none" stroke="#0a7a35" stroke-width="2"/></svg></span>
    </div>
  </div>
  <div class="abs copyright">© <b>VERDALE LODGE 37</b> - 2014. All Rights Reserved.</div>
</footer>

</body>
</html>
```